Mastering Modern Vineyard Management

size of the ad - 8”x 10.75" plus 0.25" bleed
I would like an ad for a magazine that will stand out and make people want to read the ad.
The ad should not be crowded and people reading the ad will be able to read the text.
I would like it to be a creative and modern-day design.
the list of topics should not be the focus of the ad.
the text is attached.
If you decide to use people in the ad then please no ladies.
please note that leave over 1 inch for the bottom of the footer

```html
<!DOCTYPE html>
<html lang="en">
<head>
<meta charset="utf-8">
<title>Mastering Modern Vineyard Management – Course Ad</title>
<link href="https://fonts.googleapis.com/css2?family=Playfair+Display:wght@700&family=Poppins:wght@400;700;800&family=Oswald:wght@500&display=swap" rel="stylesheet">
<style>
  :root{
    --purple:#2d1a44;
    --navy:#26305a;
    --gold:#bf9766;
    --paper:#f2f2f2;
    --ink:#3a3a3a;
    --white:#ffffff;
    --stage:#ffffff;
  }
  *{margin:0;padding:0;box-sizing:border-box}
  html,body{width:1200px;height:2637px;overflow:hidden;background:var(--stage)}
  .ad{
    position:absolute;left:75px;top:610px;width:875px;height:1180px;
    transform:scale(1.2);transform-origin:0 0;
    background:var(--paper);overflow:hidden;
    box-shadow:0 6px 24px rgba(0,0,0,.18);
    font-family:"Poppins",sans-serif;
  }
  .backdrop{position:absolute;left:0;top:476px;width:875px;height:704px;
    background:linear-gradient(180deg,#f4f4f4 0%,#e6e6e6 45%,#ececec 75%,#f3f3f3 100%)}
  .header{position:absolute;left:0;top:0;width:875px;height:470px;
    background:linear-gradient(90deg,var(--purple) 0%,#2b2250 45%,var(--navy) 100%)}
  .header-photo{position:absolute;right:0;top:0;width:460px;height:470px;
    background:radial-gradient(ellipse at 60% 45%,#6b6f7a 0%,#34405f 35%,#24305a 70%,rgba(38,48,90,0) 100%)}
  .header-rule{position:absolute;left:0;top:470px;width:875px;height:6px;background:var(--gold)}
  .title{position:absolute;left:33px;top:22px;font-family:"Playfair Display",serif;
    font-weight:700;color:var(--white);font-size:104px;line-height:89px;letter-spacing:-1px}
  .title-rule{position:absolute;left:33px;top:310px;width:398px;height:2px;background:var(--white)}
  .subtitle{position:absolute;left:33px;top:326px;font-weight:800;color:var(--gold);
    font-size:38px;line-height:42px}
  .headline{position:absolute;left:0;width:875px;text-align:center;font-weight:800;font-size:46px;line-height:52px}
  .headline.gold{top:498px;color:var(--gold)}
  .headline.purple{top:552px;color:var(--purple)}
  .sessions{position:absolute;left:62px;top:618px;width:753px;height:52px;background:var(--gold);
    color:var(--white);font-weight:800;font-size:30px;line-height:52px;text-align:center}
  .sessions .num{color:var(--purple)}
  .start-pill{position:absolute;left:62px;top:693px;width:386px;height:90px;border-radius:30px;overflow:hidden;display:flex}
  .start-pill .label{width:238px;background:var(--gold);color:var(--white);font-weight:800;font-size:40px;line-height:90px;text-align:center}
  .start-pill .date{flex:1;background:var(--purple);color:var(--white);font-family:"Oswald",sans-serif;font-weight:500;font-size:40px;line-height:90px;text-align:center}
  .start-pill sup{font-size:16px;vertical-align:20px}
  .scholarships{position:absolute;left:65px;top:795px;color:var(--purple);font-weight:700;font-size:22px}
  .early-title{position:absolute;left:497px;top:693px;color:var(--purple);font-weight:800;font-size:28px}
  .early-text{position:absolute;left:498px;top:742px;color:var(--gold);font-weight:700;font-size:21px;line-height:26px}
  .topics-title{position:absolute;left:0;top:848px;width:875px;text-align:center;font-weight:700;font-size:28px;letter-spacing:5px;color:var(--purple)}
  .topics-title span{color:var(--gold)}
  .topics-rule{position:absolute;left:206px;top:893px;width:464px;height:1px;background:var(--ink)}
  .topics-divider{position:absolute;left:452px;top:915px;width:2px;height:145px;background:linear-gradient(180deg,rgba(90,90,90,0),#666 50%,rgba(90,90,90,0))}
  .topic-list{position:absolute;top:918px;list-style:none;font-size:15.5px;color:var(--ink);line-height:26px}
  .topic-list.left{left:74px}
  .topic-list.right{left:596px}
  .topic-list li{display:flex;align-items:center;gap:18px}
  .topic-list svg{flex:none}
</style>
</head>
<body>
<div class="ad">
  <div class="backdrop" role="img" aria-label="Faint grey vineyard landscape photograph"></div>
  <div class="header"></div>
  <div class="header-photo" role="img" aria-label="Man's hands cradling a bunch of grapes"></div>
  <div class="header-rule"></div>

  <h1 class="title">WINE<br>ESTATE<br>COURSE</h1>
  <div class="title-rule"></div>
  <p class="subtitle">MASTERING MODERN<br>VINEYARD<br>MANAGEMENT</p>

  <p class="headline gold">INVESTING IN KNOWLEDGE IS</p>
  <p class="headline purple">INVESTING IN OPPORTUNITIES</p>
  <p class="sessions">BROOKVALE <span class="num">10</span> TUESDAY EVENINGS SESSIONS</p>

  <div class="start-pill">
    <span class="label">STARTING</span>
    <span class="date">28<sup>TH</sup> FEB</span>
  </div>
  <p class="scholarships">LIMITED PARTIAL SCHOLARSHIPS</p>

  <p class="early-title">EARLY BIRD SPECIAL</p>
  <p class="early-text">FOR THOSE THAT STARTED OR<br>WOULD LIKE TO GO INTO WINE<br>GROWING</p>

  <p class="topics-title">TOPICS: <span>PARTIAL LISTING</span></p>
  <div class="topics-rule"></div>
  <div class="topics-divider"></div>

  <ul class="topic-list left">
    <li><svg width="12" height="12" viewBox="0 0 12 12"><circle cx="6" cy="6" r="6" fill="#bf9766"/><path d="M3.3 6.2l1.8 1.8 3.6-3.8" stroke="#fff" stroke-width="1.4" fill="none"/></svg>Vineyard site selection</li>
    <li><svg width="12" height="12" viewBox="0 0 12 12"><circle cx="6" cy="6" r="6" fill="#bf9766"/><path d="M3.3 6.2l1.8 1.8 3.6-3.8" stroke="#fff" stroke-width="1.4" fill="none"/></svg>Soil analysis</li>
    <li><svg width="12" height="12" viewBox="0 0 12 12"><circle cx="6" cy="6" r="6" fill="#bf9766"/><path d="M3.3 6.2l1.8 1.8 3.6-3.8" stroke="#fff" stroke-width="1.4" fill="none"/></svg>Irrigation</li>
    <li><svg width="12" height="12" viewBox="0 0 12 12"><circle cx="6" cy="6" r="6" fill="#bf9766"/><path d="M3.3 6.2l1.8 1.8 3.6-3.8" stroke="#fff" stroke-width="1.4" fill="none"/></svg>Pruning</li>
    <li><svg width="12" height="12" viewBox="0 0 12 12"><circle cx="6" cy="6" r="6" fill="#bf9766"/><path d="M3.3 6.2l1.8 1.8 3.6-3.8" stroke="#fff" stroke-width="1.4" fill="none"/></svg>Canopy management</li>
  </ul>
  <ul class="topic-list right">
    <li><svg width="12" height="12" viewBox="0 0 12 12"><circle cx="6" cy="6" r="6" fill="#bf9766"/><path d="M3.3 6.2l1.8 1.8 3.6-3.8" stroke="#fff" stroke-width="1.4" fill="none"/></svg>Wine law basics</li>
    <li><svg width="12" height="12" viewBox="0 0 12 12"><circle cx="6" cy="6" r="6" fill="#bf9766"/><path d="M3.3 6.2l1.8 1.8 3.6-3.8" stroke="#fff" stroke-width="1.4" fill="none"/></svg>Choosing rootstock</li>
    <li><svg width="12" height="12" viewBox="0 0 12 12"><circle cx="6" cy="6" r="6" fill="#bf9766"/><path d="M3.3 6.2l1.8 1.8 3.6-3.8" stroke="#fff" stroke-width="1.4" fill="none"/></svg>Pest control</li>
    <li><svg width="12" height="12" viewBox="0 0 12 12"><circle cx="6" cy="6" r="6" fill="#bf9766"/><path d="M3.3 6.2l1.8 1.8 3.6-3.8" stroke="#fff" stroke-width="1.4" fill="none"/></svg>Dealing with buyers</li>
    <li><svg width="12" height="12" viewBox="0 0 12 12"><circle cx="6" cy="6" r="6" fill="#bf9766"/><path d="M3.3 6.2l1.8 1.8 3.6-3.8" stroke="#fff" stroke-width="1.4" fill="none"/></svg>Harvest fundamentals</li>
  </ul>
</div>
</body>
</html>
```